Creation of brand identity and website "Tandem K"

I am currently seeking an brand, identity and web design for a new project called Tandem K. This is a brand new concept from scratch and you have free-reign on the whole design process, taking into account my preference below.

Must include the name "Tandem K", or "Tandem K: Or the year I woke Up". Kudos is this forms part of the brands logo

Design that can be easily scaled to potentially include: a blog, timeline and vlogs.

Minimal but effective use of colour (however any colours and combinations permitted

Use of icons/graphics over text wherever possible

Minimal use of frames and borders

I appreciate this is a fairly wide scope so please contact me on marblefinch@postwillow.com with any questions or more information on what the project is.

Target Market(s)

Male and Female 20-40
Blog readers
Selfhelp

Industry/Entity Type

Seeking

Number of Pages Required

1 page

Font styles to use
Serif
Sans Serif

Requirements
Must have
• It is in effect a blog design, so about me section, recent blog / archived posts, reader comments / Q and A section.
• A coded design would be appreciated to make my life easier however I have left the design as uncoded as getting the right design matters more to me and I want to keep the project open to as many designers as possible
Nice to have
• See project description for other details and please ask if you need anything else :)
Should not have
• Mustn't be cluttered or feel fussy
• Promote icons over text
• Frames / multiple borders

```html
<!DOCTYPE html>
<html lang="en">
<head>
<meta charset="utf-8">
<title>Tandem K: Or the year I woke Up</title>
<link rel="stylesheet" href="https://fonts.googleapis.com/css2?family=Oswald:wght@300;400;500&family=Lato:ital,wght@0,400;0,700;1,400&display=swap">
<style>
:root{
  --navy:#243a5e;
  --navy-dark:#1d2f4d;
  --yellow:#f4b922;
  --ink:#333b47;
  --muted:#666c74;
  --line:#dcdde0;
  --page:#f6f6f7;
  --white:#ffffff;
  --grey-bar:#6b6d70;
  --count-blue:#3b6bb5;
  --count-red:#e2523f;
  --count-sky:#2aa3df;
  --count-grey:#555555;
}
*{box-sizing:border-box;margin:0;padding:0}
html,body{width:700px;height:1200px;overflow:hidden}
body{position:relative;background:var(--page);font-family:'Lato',sans-serif;color:var(--ink)}

/* Header */
.site-header{position:absolute;top:0;left:0;width:700px;height:40px;background:var(--white)}
.brand{position:absolute;left:76px;top:7px;font-family:'Oswald',sans-serif;font-weight:400;font-size:19px;color:var(--navy);letter-spacing:.2px}
.main-nav{position:absolute;left:326px;top:0;display:flex;height:40px}
.main-nav a{display:block;height:40px;line-height:38px;font-family:'Oswald',sans-serif;font-weight:300;font-size:10px;color:var(--navy);text-decoration:none;padding:0 10px;margin-right:10px}
.main-nav a.active{background:var(--navy);color:var(--white);border-bottom:3px solid var(--yellow);margin-right:12px}

/* Hero */
.hero{position:absolute;top:40px;left:0;width:700px;height:210px;background:linear-gradient(100deg,#4e6180 0%,#6b7c96 45%,#8290a4 70%,#5d6d86 100%)}
.hero-portrait{position:absolute;left:76px;top:29px;width:157px;height:157px;border:3px solid #d9dde3;background:linear-gradient(160deg,#c9d5e0,#8aa3bb 60%,#6e8aa6)}
.hero-title{position:absolute;left:255px;top:24px;font-family:'Oswald',sans-serif;font-weight:400;font-size:17px;color:var(--yellow)}
.hero-text{position:absolute;left:255px;top:57px;width:368px;font-size:8.2px;line-height:12.2px;color:#eef1f5}
.btn{display:inline-block;background:var(--navy);color:var(--white);font-family:'Oswald',sans-serif;font-weight:400;text-decoration:none;text-align:center}
.hero .btn{position:absolute;left:255px;top:159px;width:60px;height:24px;line-height:24px;font-size:10.5px}

/* Blog column */
.section-bar{position:absolute;left:76px;top:274px;width:361px;height:19px;background:var(--navy);color:var(--white);font-family:'Oswald',sans-serif;font-weight:400;font-size:12px;line-height:19px;padding-left:9px}
.section-bar svg{position:absolute;right:6px;top:4px}
.post{position:absolute;left:77px;width:360px;height:146px;background:var(--white);border:1px solid var(--line)}
.post-image{position:absolute;left:8px;top:10px;width:136px;height:122px;border:3px solid #e6e7e9}
.post-body{position:absolute;left:154px;top:0;width:197px}
.post-title{margin-top:7px;font-family:'Oswald',sans-serif;font-weight:400;font-size:11.2px;color:var(--navy);padding-bottom:6px;border-bottom:1px solid var(--line)}
.post-meta{display:flex;align-items:center;height:22px;font-size:7.4px;color:var(--ink)}
.post-meta .sep{width:1px;height:14px;background:#999;margin:0 7px}
.post-meta svg{margin-right:5px}
.post-excerpt{font-size:7.2px;line-height:12px;color:var(--muted);margin-top:4px;height:38px}
.counts{position:absolute;left:0;top:98px;display:flex}
.count{width:25px;margin-right:6px;text-align:center}
.count b{display:block;height:16px;line-height:14px;font-weight:400;font-size:7.4px;border:1px solid;border-radius:1px;background:var(--white)}
.count i{display:block;margin-top:3px;height:9px;line-height:8px;font-style:normal;font-size:6px;border:1px solid #cfd1d4;color:#555;border-radius:1px}
.c-blue b{color:var(--count-blue);border-color:var(--count-blue)}
.c-red b{color:var(--count-red);border-color:var(--count-red)}
.c-sky b{color:var(--count-sky);border-color:var(--count-sky)}
.c-grey b{color:var(--count-grey);border-color:var(--count-grey)}
.share{position:absolute;left:160px;top:97px;font-size:7.4px;color:var(--ink);display:flex;align-items:center;gap:5px}
.post .btn{position:absolute;left:139px;top:112px;width:57px;height:21px;line-height:21px;font-size:8.4px;border-radius:2px}

.load-more{position:absolute;left:77px;top:1126px;width:360px;height:25px;background:var(--yellow);display:flex;align-items:center;justify-content:center;gap:6px;font-family:'Oswald',sans-serif;font-weight:400;font-size:8.6px;color:var(--navy)}

/* Sidebar */
.widget{position:absolute;left:451px;width:172px;background:var(--white);border:1px solid var(--line)}
.widget-title{font-family:'Oswald',sans-serif;font-weight:400;font-size:11.2px;line-height:16px;color:var(--navy)}
.newsletter{top:274px;height:86px;padding:6px 8px}
.email-field{margin-top:7px;height:21px;border:1px solid var(--line);font-size:6.8px;color:#999;line-height:19px;padding-left:6px}
.newsletter .btn{margin-top:7px;width:58px;height:21px;line-height:21px;font-size:8.4px}

.popular{top:377px;height:233px}
.popular-head{height:20px;background:var(--grey-bar);color:var(--white);text-align:center;font-family:'Oswald',sans-serif;font-size:10.6px;line-height:20px}
.popular-tabs{display:flex;height:21px;background:var(--yellow);font-family:'Oswald',sans-serif;font-size:8px;line-height:21px;color:var(--navy)}
.popular-tabs span{text-align:center}
.popular-tabs .on{position:relative;background:var(--navy);color:var(--white);width:53px}
.popular-tabs .on:after{content:"";position:absolute;left:24px;bottom:-5px;border:5px solid transparent;border-bottom:0;border-top-color:var(--navy)}
.pop-list{padding:12px 0 0 7px}
.pop-item{display:flex;align-items:center;height:46px;margin-bottom:6px}
.pop-thumb{width:46px;height:46px;border:2px solid #e6e7e9;flex:none}
.pop-item p{margin-left:11px;font-style:italic;font-size:7.2px;line-height:10.8px;color:var(--ink);white-space:nowrap}
.view-all{position:absolute;right:8px;bottom:10px;font-size:7.6px;font-weight:700;color:var(--navy);text-decoration:underline}

.follow{top:628px;height:65px;border-top:4px solid #e6e7e9;border-bottom:4px solid #e6e7e9;padding:6px 7px}
.social-row{display:flex;gap:12px;margin-top:8px}
.social-row span{display:block;width:22px;height:22px;background:var(--navy)}

.archives{top:710px;height:138px;padding:6px 8px}
.archives ul{list-style:none;margin-top:5px}
.archives li{font-size:7.4px;font-weight:700;color:var(--ink);height:15.5px;line-height:15px;border-bottom:1px solid #ececee}
.archives li:last-child{border-bottom:0}

.tags{top:865px;height:108px;padding:6px 8px}
.tag-list{display:flex;flex-wrap:wrap;gap:7px 4px;margin-top:7px;width:154px}
.tag-list span{display:block;height:19px;line-height:19px;background:var(--yellow);color:var(--navy);font-family:'Oswald',sans-serif;font-size:10px;padding:0;text-align:center;white-space:nowrap}

.ad-space{position:absolute;left:451px;top:990px;width:172px;height:115px;background:linear-gradient(170deg,#7a4a2a 0%,#3a2418 45%,#120d0c 100%)}

.site-footer{position:absolute;left:0;top:1173px;width:700px;height:27px;background:var(--navy);color:var(--white);font-family:'Oswald',sans-serif;font-weight:300;font-size:7.8px;text-align:center;line-height:27px}
</style>
</head>
<body>

<header class="site-header">
  <div class="brand">Tandem K</div>
  <nav class="main-nav">
    <a class="active" href="#">About Me</a>
    <a href="#">Recent Blog</a>
    <a href="#">Reader Comments</a>
    <a href="#">Contact Us</a>
  </nav>
</header>

<section class="hero" role="img" aria-label="Background photo of a couple running along a beach at sunset">
  <div class="hero-portrait" role="img" aria-label="Portrait photo of the blog author"></div>
  <h1 class="hero-title">About Me</h1>
  <p class="hero-text">Lorem ipsum dolor sit amet, consectetuer adipiscing elit, sed diam nonummy nibh euismod alme tincidunt ut laoreet dolore magna aliquam erat volutpat. Ut wisi enim ad minim veniam, quis dol nostrud exerci tation ullamcorper suscipit lobortis nisl ut aliquip ex ea commodo consequat list Duis autem vel eum iriure dolor in hendrerit in vulputate velit esse molestie consequat, vel alm illum dolore eu feugiat nulla facilisis at vero eros et accumsan et iusto odio dignissim qui blandit illum dolore eu feugiat nulla facilisis at vero eros et accumsan et iusto odio dignissim qui blandit praesent luptatum zzril delenit augue duis dolore te feugait nulla facilisi.</p>
  <a class="btn" href="#">Read More</a>
</section>

<h2 class="section-bar">Recent Blog Posts
  <svg width="12" height="11" viewBox="0 0 12 11"><rect x="0.5" y="0.5" width="9" height="10" fill="none" stroke="#f4b922"/><path d="M2 3h6M2 5h6M2 7h4" stroke="#f4b922"/><path d="M7 9l4-5" stroke="#f4b922" stroke-width="1.5"/></svg>
</h2>

<article class="post" style="top:300px">
  <div class="post-image" role="img" aria-label="Photo of a woman stretching her arms towards the bright sky" style="background:linear-gradient(200deg,#f8f2dc,#8fb6d8 45%,#3d6fa6)"></div>
  <div class="post-body">
    <h3 class="post-title">Lorem ipsum dolor sit amet consecit dolor</h3>
    <div class="post-meta"><svg width="7" height="7"><rect width="7" height="7" fill="#f4b922"/></svg>June 18, 2016<span class="sep"></span><svg width="8" height="7"><ellipse cx="4" cy="3.2" rx="4" ry="3.2" fill="#f4b922"/></svg>No Comments</div>
    <p class="post-excerpt">Lorem ipsum dolor sit amet, consecit adipiscing elit, sed do eiusmod tempor incidimen labore n dolorme laboris ni ut ullamco Neque porro quisquam est, qui dolorem ipsum</p>
    <div class="counts"><div class="count c-blue"><b>560</b><i>Like</i></div><div class="count c-red"><b>36</b><i>+1</i></div><div class="count c-sky"><b>456</b><i>Post</i></div><div class="count c-grey"><b>1066</b><i>Email</i></div></div>
    <div class="share">Share <svg width="12" height="9" viewBox="0 0 12 9"><path d="M1 8C2 4 5 3 8 3V1l4 3.5L8 8V6C5 6 3 6.5 1 8z" fill="#f4b922"/></svg></div>
    <a class="btn" href="#">Read More</a>
  </div>
</article>

<article class="post" style="top:464px">
  <div class="post-image" role="img" aria-label="Photo of a young woman with pink hair on a sunny beach" style="background:linear-gradient(160deg,#f3e1cf,#e2b7a4 50%,#c89a8a)"></div>
  <div class="post-body">
    <h3 class="post-title">Lorem ipsum dolor sit amet consecit dolor</h3>
    <div class="post-meta"><svg width="7" height="7"><rect width="7" height="7" fill="#f4b922"/></svg>June 22, 2016<span class="sep"></span><svg width="8" height="7"><ellipse cx="4" cy="3.2" rx="4" ry="3.2" fill="#f4b922"/></svg>No Comments</div>
    <p class="post-excerpt">Lorem ipsum dolor sit amet, consecit adipiscing elit, sed do eiusmod tempor incidimen labore n dolorme laboris ni ut ullamco Neque porro quisquam est, qui dolorem ipsum</p>
    <div class="counts"><div class="count c-blue"><b>560</b><i>Like</i></div><div class="count c-red"><b>36</b><i>+1</i></div><div class="count c-sky"><b>456</b><i>Post</i></div><div class="count c-grey"><b>1066</b><i>Email</i></div></div>
    <div class="share">Share <svg width="12" height="9" viewBox="0 0 12 9"><path d="M1 8C2 4 5 3 8 3V1l4 3.5L8 8V6C5 6 3 6.5 1 8z" fill="#f4b922"/></svg></div>
    <a class="btn" href="#">Read More</a>
  </div>
</article>

<article class="post" style="top:629px">
  <div class="post-image" role="img" aria-label="Black and white photo of a smiling couple close together" style="background:linear-gradient(135deg,#1e1e1e,#6a6a6a 55%,#d8d8d8)"></div>
  <div class="post-body">
    <h3 class="post-title">Lorem ipsum dolor sit amet consecit dolor</h3>
    <div class="post-meta"><svg width="7" height="7"><rect width="7" height="7" fill="#f4b922"/></svg>June 26, 2016<span class="sep"></span><svg width="8" height="7"><ellipse cx="4" cy="3.2" rx="4" ry="3.2" fill="#f4b922"/></svg>No Comments</div>
    <p class="post-excerpt">Lorem ipsum dolor sit amet, consecit adipiscing elit, sed do eiusmod tempor incidimen labore n dolorme laboris ni ut ullamco Neque porro quisquam est, qui dolorem ipsum</p>
    <div class="counts"><div class="count c-blue"><b>560</b><i>Like</i></div><div class="count c-red"><b>36</b><i>+1</i></div><div class="count c-sky"><b>456</b><i>Post</i></div><div class="count c-grey"><b>1066</b><i>Email</i></div></div>
    <div class="share">Share <svg width="12" height="9" viewBox="0 0 12 9"><path d="M1 8C2 4 5 3 8 3V1l4 3.5L8 8V6C5 6 3 6.5 1 8z" fill="#f4b922"/></svg></div>
    <a class="btn" href="#">Read More</a>
  </div>
</article>

<article class="post" style="top:794px">
  <div class="post-image" role="img" aria-label="Photo of a family playing in a field of red poppies under a blue sky" style="background:linear-gradient(180deg,#5aa6dc,#a9d2ee 45%,#7ea353 75%,#c8452c)"></div>
  <div class="post-body">
    <h3 class="post-title">Lorem ipsum dolor sit amet consecit dolor</h3>
    <div class="post-meta"><svg width="7" height="7"><rect width="7" height="7" fill="#f4b922"/></svg>June 30, 2016<span class="sep"></span><svg width="8" height="7"><ellipse cx="4" cy="3.2" rx="4" ry="3.2" fill="#f4b922"/></svg>No Comments</div>
    <p class="post-excerpt">Lorem ipsum dolor sit amet, consecit adipiscing elit, sed do eiusmod tempor incidimen labore n dolorme laboris ni ut ullamco Neque porro quisquam est, qui dolorem ipsum</p>
    <div class="counts"><div class="count c-blue"><b>560</b><i>Like</i></div><div class="count c-red"><b>36</b><i>+1</i></div><div class="count c-sky"><b>456</b><i>Post</i></div><div class="count c-grey"><b>1066</b><i>Email</i></div></div>
    <div class="share">Share <svg width="12" height="9" viewBox="0 0 12 9"><path d="M1 8C2 4 5 3 8 3V1l4 3.5L8 8V6C5 6 3 6.5 1 8z" fill="#f4b922"/></svg></div>
    <a class="btn" href="#">Read More</a>
  </div>
</article>

<article class="post" style="top:960px">
  <div class="post-image" role="img" aria-label="Photo of a man with open arms at the bow of a sailing boat" style="background:linear-gradient(180deg,#e9eef3,#b9c8d6 45%,#4d6d8e 75%,#d8dde2)"></div>
  <div class="post-body">
    <h3 class="post-title">Lorem ipsum dolor sit amet consecit dolor</h3>
    <div class="post-meta"><svg width="7" height="7"><rect width="7" height="7" fill="#f4b922"/></svg>July 01, 2016<span class="sep"></span><svg width="8" height="7"><ellipse cx="4" cy="3.2" rx="4" ry="3.2" fill="#f4b922"/></svg>No Comments</div>
    <p class="post-excerpt">Lorem ipsum dolor sit amet, consecit adipiscing elit, sed do eiusmod tempor incidimen labore n dolorme laboris ni ut ullamco Neque porro quisquam est, qui dolorem ipsum</p>
    <div class="counts"><div class="count c-blue"><b>560</b><i>Like</i></div><div class="count c-red"><b>36</b><i>+1</i></div><div class="count c-sky"><b>456</b><i>Post</i></div><div class="count c-grey"><b>1066</b><i>Email</i></div></div>
    <div class="share">Share <svg width="12" height="9" viewBox="0 0 12 9"><path d="M1 8C2 4 5 3 8 3V1l4 3.5L8 8V6C5 6 3 6.5 1 8z" fill="#f4b922"/></svg></div>
    <a class="btn" href="#">Read More</a>
  </div>
</article>

<div class="load-more">
  <svg width="11" height="11" viewBox="0 0 12 12"><g stroke="#243a5e" stroke-width="1.6" stroke-linecap="round"><path d="M6 1v2.5M6 8.5V11M1 6h2.5M8.5 6H11M2.5 2.5l1.8 1.8M7.7 7.7l1.8 1.8M2.5 9.5l1.8-1.8M7.7 4.3l1.8-1.8"/></g></svg>
  Load More Blogs
</div>

<aside>
  <section class="widget newsletter">
    <h3 class="widget-title">Sign Up For Free Newsletter</h3>
    <div class="email-field">Enter Your Email Address</div>
    <a class="btn" href="#">SUBSCRIBE</a>
  </section>

  <section class="widget popular">
    <div class="popular-head">Popular</div>
    <div class="popular-tabs"><span class="on">Page Views</span><span style="width:66px">Social Shares#</span><span style="width:51px">Comments</span></div>
    <div class="pop-list">
      <div class="pop-item"><div class="pop-thumb" role="img" aria-label="Photo of a woman in a green meadow" style="background:linear-gradient(160deg,#e8efd0,#8dae4c 60%,#4f7a2a)"></div><p>Lorem ipsum dolor sit ame<br>consectetuer adipiscing<br>Dolor sit almet</p></div>
      <div class="pop-item"><div class="pop-thumb" role="img" aria-label="Photo of a woman in a white dress outdoors" style="background:linear-gradient(160deg,#f5f3e8,#c9d4a0 60%,#7f9a4a)"></div><p>Lorem ipsum dolor sit ame<br>consectetuer adipiscing<br>Dolor sit almet</p></div>
      <div class="pop-item"><div class="pop-thumb" role="img" aria-label="Photo of a smiling young man" style="background:linear-gradient(160deg,#eeeeee,#c7b7a6 60%,#7d6b5c)"></div><p>Lorem ipsum dolor sit ame<br>consectetuer adipiscing</p></div>
    </div>
    <span class="view-all">View All &gt;&gt;</span>
  </section>

  <section class="widget follow">
    <h3 class="widget-title">Follow Us</h3>
    <div class="social-row"><span></span><span></span><span></span><span></span><span></span></div>
  </section>

  <section class="widget archives">
    <h3 class="widget-title">Archives</h3>
    <ul><li>July 2016</li><li>June 2016</li><li>May 2016</li><li>April 2016</li><li>March 2016</li><li>February 2016</li><li>January 2016</li></ul>
  </section>

  <section class="widget tags">
    <h3 class="widget-title">Popular Tags</h3>
    <div class="tag-list"><span style="width:33px">SIT</span><span style="width:47px">DOLOR</span><span style="width:66px">ALMETSIT</span><span style="width:48px">DOLOR</span><span style="width:49px">ELIT</span><span style="width:42px">SIT</span><span style="width:40px">ELIT</span><span style="width:50px">ALMETS</span></div>
  </section>

  <div class="ad-space" role="img" aria-label="Advertisement photo of a pickup truck at sunset"></div>
</aside>

<footer class="site-footer">© 2016 Tandem K. All Rights Reserved.</footer>

</body>
</html>
```